Pressure Washing Hog Confinements

We clean and disinfect Hog confinements in-order to receive new pigs.

Needs to emphasis Clean Healthy barns (pigs), work done in timely manner, 100% satisfied, Bio-security rules followed. I do not have specific colors, no logo's.

Contact Information will be sent once design is agreed on.
Business Name - Brandt & Daughters Power Washing
Phone Number - Send latter
E-mail - Send latter
Web Address - Send latter

Target Market(s)

Farmers

Industry/Entity Type

Business

Requirements
Must have
• We are Insured
Bio-Security
100% Satisfied
Water Conservation

Size - 2 sided Postcard 8.5" x 5.5"
Nice to have
• I want to emphasize healthy and happy pigs because of a quality job done. Picture of pigs dose not need to be used but may be just an example.

Also attached is picture of a barn I would like to see used. on the back side. Every owner seeing this will know this is a hog barn and have an idea what we do.

```html
<!DOCTYPE html>
<html lang="en">
<head>
<meta charset="utf-8">
<title>Brandt &amp; Daughters Power Washing – Postcard</title>
<link rel="stylesheet" href="https://fonts.googleapis.com/css2?family=Roboto+Condensed:wght@400;700&family=Arimo:wght@400&family=Sansita:wght@800&display=swap">
<style>
  :root {
    --backdrop: #3a3a3a;
    --blue-deep: #0b5fb8;
    --blue-bright: #1f8fe0;
    --blue-light: #5fc0f5;
    --silver-dark: #8e939a;
    --white: #ffffff;
    --paper-top: #f4f5f7;
    --paper-bottom: #e4e6ea;
    --green-text: #2a9a2a;
    --green-dot: #6cc23a;
    --ink: #2b2b2b;
    --name-grey: #4a4a4a;
    --photo-warm-light: #b47a52;
    --photo-warm-dark: #7a4428;
    --photo-sky: #8fbde8;
    --photo-sky-pale: #c3d7ea;
  }
  * { margin: 0; padding: 0; box-sizing: border-box; }
  html, body {
    width: 1200px; height: 458px; overflow: hidden;
    background: var(--backdrop);
  }
  .canvas { position: relative; width: 1200px; height: 458px; }

  .postcard {
    position: absolute; width: 544px; height: 352px; overflow: hidden;
    box-shadow: 0 2px 8px rgba(0,0,0,.45);
  }
  .postcard svg.shapes { position: absolute; inset: 0; width: 100%; height: 100%; }

  /* Front */
  .postcard--front { left: 38px; top: 37px; }
  .front-photo {
    position: absolute; inset: 0;
    background: linear-gradient(135deg, var(--photo-warm-light) 0%, var(--photo-warm-dark) 100%);
  }
  .front-benefits {
    position: absolute; left: 20px; top: 24px;
    font-family: "Roboto Condensed", "Arial Narrow", sans-serif;
    font-weight: 700; font-size: 21px; line-height: 25.6px;
    color: var(--white); list-style: none;
  }
  .front-name {
    position: absolute; right: 20px; top: 276px;
    font-family: "Sansita", "Arial Black", sans-serif;
    font-weight: 800; font-size: 22px; line-height: 26px; color: var(--white);
  }
  .front-contact {
    position: absolute; left: 20px; top: 314px;
    font-family: "Arimo", Arial, sans-serif; font-size: 10.5px; line-height: 14px;
    color: var(--white);
  }
  .front-contact .web { margin-left: 24px; }

  /* Back */
  .postcard--back {
    left: 618px; top: 62px;
    background: linear-gradient(180deg, var(--paper-top), var(--paper-bottom));
  }
  .back-name {
    position: absolute; left: 20px; top: 64px;
    font-family: "Sansita", "Arial Black", sans-serif;
    font-weight: 800; font-size: 21px; color: var(--name-grey);
  }
  .back-message {
    position: absolute; left: 20px; top: 94px;
    font-family: "Roboto Condensed", "Arial Narrow", sans-serif;
    font-size: 14.5px; line-height: 18.5px; color: var(--green-text);
  }
  .barn-photo {
    position: absolute; left: 0; top: 156px; width: 353px; height: 121px;
    border-radius: 0 16px 16px 0;
    background: linear-gradient(180deg, var(--photo-sky) 0%, var(--photo-sky-pale) 100%);
  }
  .back-contact {
    position: absolute; left: 32px; top: 287px;
    font-family: "Arimo", Arial, sans-serif; font-size: 12px; color: var(--ink);
    display: flex; align-items: center; gap: 10px;
  }
  .back-contact .dot {
    width: 8px; height: 8px; border-radius: 50%; background: var(--green-dot);
  }
  .back-web {
    position: absolute; right: 18px; top: 322px;
    font-family: "Arimo", Arial, sans-serif; font-size: 11.5px; color: var(--white);
  }
  .indicia {
    position: absolute; left: 475px; top: 19px; width: 46px; height: 46px;
    border: 1px solid var(--ink); background: var(--white);
    font-family: "Arimo", Arial, sans-serif; font-size: 5px; line-height: 6.4px;
    text-align: center; color: var(--ink); padding-top: 4px;
  }
  .indicia .paid { font-size: 7px; line-height: 8px; }
  .address-box {
    position: absolute; left: 430px; top: 88px; width: 91px; height: 46px;
    border: 1px solid var(--ink); background: var(--white);
    font-family: "Arimo", Arial, sans-serif; font-size: 7px; line-height: 9px;
    color: var(--ink); padding: 14px 0 0 6px;
  }
</style>
</head>
<body>
<main class="canvas">

  <section class="postcard postcard--front" aria-label="Postcard front">
    <div class="front-photo" role="img" aria-label="Photo of a worker checking a water sample in a hog barn with pigs behind the pen rails"></div>
    <svg class="shapes" viewBox="0 0 544 352" aria-hidden="true">
      <defs>
        <linearGradient id="frontBlue" x1="0" y1="0" x2="1" y2="0">
          <stop offset="0" stop-color="var(--blue-deep)"/>
          <stop offset=".55" stop-color="var(--blue-bright)"/>
          <stop offset="1" stop-color="var(--blue-deep)"/>
        </linearGradient>
        <linearGradient id="frontSilver" x1="0" y1="0" x2="1" y2="0">
          <stop offset="0" stop-color="var(--silver-dark)"/>
          <stop offset=".5" stop-color="var(--white)"/>
          <stop offset="1" stop-color="var(--silver-dark)"/>
        </linearGradient>
      </defs>
      <path class="top-swoosh" d="M220,0 H544 V54 C470,20 360,8 220,0 Z" fill="url(#frontBlue)"/>
      <path class="top-silver" d="M230,2 C360,8 470,22 544,58 V66 C470,30 360,12 230,2 Z" fill="url(#frontSilver)"/>
      <path class="bottom-silver" d="M0,272 C140,292 300,326 544,288 V298 C300,334 140,302 0,282 Z" fill="url(#frontSilver)"/>
      <path class="bottom-band" d="M0,282 C140,302 300,336 544,298 V352 H0 Z" fill="url(#frontBlue)"/>
    </svg>
    <ul class="front-benefits">
      <li>We are Insured</li>
      <li>Bio-Security</li>
      <li>100% Satisfied</li>
      <li>Water Conservation</li>
    </ul>
    <p class="front-name">Brandt &amp; Daughters</p>
    <div class="front-contact">
      <p>555 012 3456</p>
      <p>info@brandtdaughters.com<span class="web">www.brandtdaughters.com</span></p>
    </div>
  </section>

  <section class="postcard postcard--back" aria-label="Postcard back">
    <svg class="shapes" viewBox="0 0 544 352" aria-hidden="true">
      <defs>
        <linearGradient id="backBlue" x1="0" y1="0" x2="1" y2="0">
          <stop offset="0" stop-color="var(--blue-deep)"/>
          <stop offset=".5" stop-color="var(--blue-light)"/>
          <stop offset="1" stop-color="var(--blue-deep)"/>
        </linearGradient>
        <linearGradient id="backSilver" x1="0" y1="0" x2="1" y2="0">
          <stop offset="0" stop-color="var(--silver-dark)"/>
          <stop offset=".5" stop-color="var(--white)"/>
          <stop offset="1" stop-color="var(--silver-dark)"/>
        </linearGradient>
      </defs>
      <path class="top-swoosh" d="M0,0 H360 C250,8 110,22 0,48 Z" fill="url(#backBlue)"/>
      <path class="top-silver" d="M0,48 C110,22 250,8 360,0 H372 C250,12 110,30 0,58 Z" fill="url(#backSilver)"/>
      <path class="bottom-silver" d="M0,304 C160,326 360,300 544,270 V280 C360,310 160,336 0,314 Z" fill="url(#backSilver)"/>
      <path class="bottom-band" d="M0,316 C160,338 360,312 544,282 V352 H0 Z" fill="url(#backBlue)"/>
    </svg>
    <p class="back-name">Brandt &amp; Daughters</p>
    <p class="back-message">Clean Healthy barns (pigs), work done<br>in timely manner, 100% satisfied,<br>Bio-security rules followed</p>
    <div class="barn-photo" role="img" aria-label="Photo of a long hog confinement barn with grain bins under a blue sky"></div>
    <p class="back-contact"><span>555 012 3456</span><span class="dot"></span><span>info@brandtdaughters.com</span></p>
    <p class="back-web">www.brandtdaughters.com</p>
    <div class="indicia">PRSRT STD<br>ECRWSS<br>U.S.POSTAGE<br><span class="paid">PAID</span><br>EDDM Retail</div>
    <div class="address-box">Local<br>Postal Customer</div>
  </section>

</main>
</body>
</html>
```